Veltrane Group Business Card Design

The CEO is looking for a new trendy look for his business card.
You can stay with current branding or come up with something new/creative. It can be 3D, including Medical Office buildings. You can use our logo in a variety of colors. Please include name, title, company name, company website, email address, cell number

Target Market(s)

Real Estate Development and Construction

Industry/Entity Type

Health care real estate

Contact Information for Business Card

Rohesh Kamdar, CEO M-604.781.2249 E-roheshkamdar@veltrane.com Address:4180 Lindqvist Ave, Tampa, FL 33482 www.veltrane.com

Font styles to use
Other font styles liked:
• Be creative

Requirements
Must have
• Creative, trendy look
Nice to have
• Please go to our website to get a feel- www. veltrane.com
Should not have
• small fonts

```html
<!DOCTYPE html>
<html lang="en">
<head>
<meta charset="UTF-8">
<title>Veltrane Group Business Card</title>
<link href="https://fonts.googleapis.com/css2?family=Poppins:wght@400;700;800&display=swap" rel="stylesheet">
<style>
  :root {
    --page-bg: #2a2a2c;
    --card-bg: #0d0d0e;
    --brand-red: #c1222e;
    --text-white: #f4f4f4;
    --logo-silver: #d9d9d9;
    --divider: #3c3c3e;
  }
  * { margin: 0; padding: 0; box-sizing: border-box; }
  html, body {
    width: 1200px;
    height: 900px;
    overflow: hidden;
    background: var(--page-bg);
    font-family: "Poppins", sans-serif;
  }
  .sheet {
    width: 1200px;
    height: 900px;
    display: flex;
    flex-direction: column;
    align-items: center;
    justify-content: center;
    gap: 40px;
  }
  .card {
    width: 700px;
    height: 400px;
    background: var(--card-bg);
    border-radius: 22px;
    position: relative;
    overflow: hidden;
  }
  .card-front {
    display: flex;
    align-items: center;
  }
  .front-brand {
    width: 330px;
    display: flex;
    justify-content: flex-end;
    padding-right: 34px;
  }
  .wordmark {
    display: flex;
    align-items: center;
    gap: 10px;
    font-weight: 800;
    line-height: 1;
    letter-spacing: -0.5px;
  }
  .wordmark-square {
    width: 14px;
    height: 14px;
    flex: none;
  }
  .front-brand .wordmark { font-size: 34px; color: var(--brand-red); }
  .front-brand .wordmark-square { background: var(--brand-red); }
  .front-divider {
    width: 1px;
    height: 170px;
    background: linear-gradient(to bottom, transparent, var(--divider) 20%, var(--divider) 80%, transparent);
  }
  .front-details {
    padding-left: 34px;
    color: var(--text-white);
  }
  .person-name {
    font-weight: 700;
    font-size: 24px;
    color: var(--brand-red);
    line-height: 1.1;
  }
  .person-title {
    font-size: 17px;
    margin-bottom: 10px;
  }
  .contact-list { list-style: none; }
  .contact-item {
    display: flex;
    align-items: center;
    gap: 10px;
    font-size: 15px;
    line-height: 1.6;
  }
  .contact-icon { width: 15px; height: 15px; flex: none; }
  .contact-address {
    margin-top: 14px;
    padding-left: 25px;
    font-size: 15px;
    line-height: 1.35;
  }
  .card-back {
    display: flex;
    align-items: center;
    justify-content: center;
  }
  .card-back .wordmark { font-size: 58px; color: var(--logo-silver); gap: 16px; }
  .card-back .wordmark-square { width: 22px; height: 22px; background: var(--logo-silver); }
</style>
</head>
<body>
<main class="sheet">
  <section class="card card-front" aria-label="Business card front">
    <div class="front-brand">
      <div class="wordmark"><span class="wordmark-square"></span><span>Veltrane Group</span></div>
    </div>
    <div class="front-divider"></div>
    <div class="front-details">
      <h1 class="person-name">Rohesh Kamdar</h1>
      <p class="person-title">CEO</p>
      <ul class="contact-list">
        <li class="contact-item">
          <svg class="contact-icon" viewBox="0 0 24 24" aria-hidden="true"><path fill="var(--brand-red)" d="M6.6 10.8a15.1 15.1 0 0 0 6.6 6.6l2.2-2.2c.3-.3.7-.4 1-.2 1.1.4 2.3.6 3.6.6.6 0 1 .4 1 1V20c0 .6-.4 1-1 1A17 17 0 0 1 3 4c0-.6.4-1 1-1h3.5c.6 0 1 .4 1 1 0 1.3.2 2.5.6 3.6.1.3 0 .7-.2 1l-2.3 2.2z"/></svg>
          <span>604.781.2249</span>
        </li>
        <li class="contact-item">
          <svg class="contact-icon" viewBox="0 0 24 24" aria-hidden="true"><path fill="var(--brand-red)" d="M2 5h20v14H2z"/><path fill="none" stroke="var(--card-bg)" stroke-width="1.8" d="M2.5 5.5 12 13l9.5-7.5"/></svg>
          <span>roheshkamdar@veltrane.com</span>
        </li>
        <li class="contact-item">
          <svg class="contact-icon" viewBox="0 0 24 24" aria-hidden="true"><g fill="none" stroke="var(--brand-red)" stroke-width="2"><circle cx="12" cy="12" r="9.5"/><ellipse cx="12" cy="12" rx="4.2" ry="9.5"/><path d="M2.5 12h19M4 7h16M4 17h16"/></g></svg>
          <span>www.veltrane.com</span>
        </li>
      </ul>
      <p class="contact-address">4180 Lindqvist Ave, Tampa<br>FL 33482</p>
    </div>
  </section>

  <section class="card card-back" aria-label="Business card back">
    <div class="wordmark"><span class="wordmark-square"></span><span>Veltrane Group</span></div>
  </section>
</main>
</body>
</html>
```